Business Card for Fashion House

We need a business card design for our personalize fashion service for our customers. the business card should reflect reliability, luxury and creativity.
The brand Gravetto is extracted from "Graceful Velvetto"; Gravetto provides fashion designs sprinkled with luxury and style tailored for our elite clients character profile.
Gravetto is created for those who embody class and elegance with a passion for style.
Target Market(s)
Affluent Customers
Industry/Entity Type
Fashion
Contact Information for Business Card
Samira Haddadin
Fashion Designer
Telephone: +971 4 555 0192
Mobile +971 50 555 0147
Emal info@gravetto-example.com
Website www.gravetto-example.com
Social Media Youtube g+ Facebook Instagram Pin /gravetto
Font styles to use
Other font styles liked:
- Audrey provided
Look and feel
Each slider illustrates characteristics of the customer's brand and the style your logo design should communicate.

```html
<!DOCTYPE html>
<html lang="en">
<head>
<meta charset="utf-8">
<title>Gravetto Business Card</title>
<link rel="stylesheet" href="https://fonts.googleapis.com/css2?family=Cormorant+Garamond:wght@500;600&family=Marcellus&family=Roboto:wght@400&display=swap">
<style>
  :root {
    --bg: #d6d6d6;
    --ink: #232526;
    --paper: #ffffff;
    --muted: #3a3c3d;
  }
  * { margin: 0; padding: 0; box-sizing: border-box; }
  html, body { width: 1200px; height: 852px; overflow: hidden; }
  body { background: var(--bg); position: relative; font-family: "Roboto", sans-serif; }

  .card {
    position: absolute;
    width: 520px;
    height: 300px;
    border-radius: 22px;
    overflow: hidden;
  }
  .card--back { left: 110px; top: 100px; background: var(--ink); }
  .card--front { left: 570px; top: 450px; background: var(--paper); }

  .wordmark {
    position: absolute;
    font-family: "Marcellus", serif;
    letter-spacing: 0.55em;
    font-size: 26px;
    white-space: nowrap;
  }
  .card--back .wordmark {
    color: var(--paper);
    left: 0; right: 0; top: 132px;
    text-align: center;
    padding-left: 0.55em;
  }
  .card--front .wordmark { color: var(--ink); left: 40px; top: 98px; font-size: 22px; }

  .waves { position: absolute; inset: 0; }

  .person { position: absolute; right: 28px; top: 12px; text-align: right; color: var(--ink); }
  .person__name { font-family: "Cormorant Garamond", serif; font-weight: 600; font-size: 24px; line-height: 1; }
  .person__role { font-size: 10px; margin-top: 3px; color: var(--muted); }

  .social {
    position: absolute; left: 42px; top: 148px;
    display: flex; align-items: center; gap: 7px;
    font-size: 13px; color: var(--ink);
  }
  .social__dot { width: 11px; height: 11px; border-radius: 50%; background: var(--ink); }

  .contact {
    position: absolute; right: 24px; top: 168px;
    list-style: none; color: var(--paper); font-size: 12px; line-height: 18px;
  }
  .contact li { display: flex; justify-content: flex-end; align-items: center; gap: 8px; white-space: nowrap; }
  .contact svg { width: 12px; height: 12px; flex: none; }
</style>
</head>
<body>

<section class="card card--back" aria-label="Card back">
  <div class="wordmark">GRAVETTO</div>
</section>

<section class="card card--front" aria-label="Card front">
  <svg class="waves" viewBox="0 0 520 300" preserveAspectRatio="none" aria-hidden="true">
    <path d="M520,62 C410,64 330,85 290,140 C255,195 235,245 0,250 L0,300 L520,300 Z" fill="var(--ink)"/>
    <path d="M520,76 C415,80 340,100 302,152 C268,205 248,258 0,264" fill="none" stroke="var(--paper)" stroke-width="6"/>
    <path d="M520,54 C405,56 322,78 282,134 C248,188 228,236 0,242" fill="none" stroke="var(--ink)" stroke-width="3"/>
  </svg>

  <div class="person">
    <div class="person__name">Samira Haddadin</div>
    <div class="person__role">Fashion Designer</div>
  </div>

  <div class="wordmark">GRAVETTO</div>

  <div class="social">
    <span class="social__dot"></span>
    <span>/gravetto</span>
  </div>

  <ul class="contact">
    <li>+971 4 555 0192
      <svg viewBox="0 0 12 12"><path d="M3 1 L5 3.5 L4 5 Q5.5 7 7 8 L8.5 7 L11 9 L9.5 11 Q4 10 1 2.5 Z" fill="var(--paper)"/></svg>
    </li>
    <li>+971 50 555 0147
      <svg viewBox="0 0 12 12"><rect x="3" y="0.5" width="6" height="11" rx="1.2" fill="none" stroke="var(--paper)" stroke-width="1.2"/><circle cx="6" cy="9.5" r="0.8" fill="var(--paper)"/></svg>
    </li>
    <li>info@gravetto-example.com
      <svg viewBox="0 0 12 12"><rect x="0.7" y="2.5" width="10.6" height="7.5" fill="none" stroke="var(--paper)" stroke-width="1.2"/><path d="M1 3 L6 7 L11 3" fill="none" stroke="var(--paper)" stroke-width="1.2"/></svg>
    </li>
    <li>www.gravetto-example.com
      <svg viewBox="0 0 12 12"><circle cx="6" cy="6" r="5.2" fill="none" stroke="var(--paper)" stroke-width="1.2"/><ellipse cx="6" cy="6" rx="2.2" ry="5.2" fill="none" stroke="var(--paper)" stroke-width="1"/><path d="M1 6 H11" stroke="var(--paper)" stroke-width="1"/></svg>
    </li>
  </ul>
</section>

</body>
</html>
```